QuillVane needs a dashboard page designed

Redesign the dashboard shown in the provided images.

There are two images:
- dashboard.png
- dashboard-expanded.png

NOTE: The vocabulary navigation on the left will be a very long list of words 100s, so keep that in mind when you're designing both the vocab navigation and the expanded vocab popup.

In the dashboard.png picture, there needs to be a progress chart showing the word progress like the following: review 1(show it as completed) -> review 2(show the user they are here) -> review 3(unvisited) -> review 4(unvisited)

The do-not-design-this-page.png image is for your reference only. It is not to be designed. Use it to understand the overall look and feel of the website to help you create the best dashboard page possible.
Updates

Need extra days to review

Industry/Entity Type

Education English learning

Number of Pages Required

1 page

Requirements
Must have
• The main navigation and main header cannot change between pages. See the do-not-design page for the main navigateion and header.
Should not have
• Do not add a person profile. We will not have images of our users. Keep the icons in the main navigation as they are.

```html
<!DOCTYPE html>
<html lang="en">
<head>
<meta charset="utf-8">
<title>LexiPath Tutor – Vocabulary Dashboard</title>
<link href="https://fonts.googleapis.com/css2?family=Roboto:wght@400;500;700&display=swap" rel="stylesheet">
<style>
:root{
  --ink:#1f2124;
  --text:#2b2d31;
  --muted:#6b6e73;
  --line:#e3e4e6;
  --bar:#1c1f23;
  --red:#c8161d;
  --green:#1f9d55;
  --page:#ffffff;
  --star:#e0a000;
}
*{box-sizing:border-box;margin:0;padding:0}
html,body{width:1200px;height:675px;overflow:hidden}
body{font-family:'Roboto',sans-serif;color:var(--text);background:var(--page);position:relative}
.abs{position:absolute}
.topbar{left:0;top:0;width:1200px;height:25px;background:var(--bar);color:#cfd2d6;font-size:11px;display:flex;align-items:center;justify-content:center}
.topbar .icons{position:absolute;right:10px;top:5px;display:flex;gap:14px}
.mainnav{left:0;top:25px;width:52px;height:650px;background:var(--bar)}
.navitem{width:52px;height:53px;display:flex;flex-direction:column;align-items:center;justify-content:center;color:#cfd2d6;font-size:6px;gap:3px}
.navitem.active{background:#2a2d32}
.vocab{left:52px;top:25px;width:240px;height:650px;background:#fff;border-right:1px solid var(--line)}
.select{border:1px solid #c9cbce;border-radius:3px;height:30px;display:flex;align-items:center;justify-content:space-between;padding:0 9px;font-size:11px;color:var(--text)}
.iconbtn{border:1px solid #c9cbce;border-radius:3px;width:30px;height:30px;display:flex;align-items:center;justify-content:center}
.group{position:absolute;left:18px;width:205px}
.group-head{display:flex;align-items:center;gap:8px;font-size:11px;font-weight:500;color:var(--ink);height:24px}
.group-head .info{margin-left:auto}
.word{font-size:11px;color:#45484d;height:28px;line-height:28px;border-bottom:1px solid var(--line);margin-left:22px;padding-left:0}
.word.current{border-left:2px solid var(--red);padding-left:12px;color:var(--ink)}
.title{left:323px;top:40px;font-size:28px;font-weight:700;color:var(--ink);display:flex;align-items:center;gap:10px}
.steps{left:683px;top:50px;display:flex;align-items:center;gap:8px;font-size:11px;font-weight:500}
.dots{width:20px;border-top:1px dotted #999}
.step.done{color:var(--green)}.step.cur{color:var(--ink)}.step.todo{color:#b0b2b5}
.step{display:flex;align-items:center;gap:6px}
.start{left:1068px;top:43px;width:102px;height:30px;background:var(--red);color:#fff;border-radius:3px;font-size:11px;font-weight:500;display:flex;align-items:center;justify-content:center;gap:8px}
.hr{height:1px;background:var(--line)}
.desc{left:322px;top:122px;display:flex;align-items:center;gap:12px;font-size:14px;font-weight:500;color:var(--ink)}
.analysis{left:930px;top:93px;width:270px;height:582px;border-left:1px solid var(--line);padding:30px 30px 0 30px}
.analysis h2{font-size:14px;font-weight:500;line-height:16px;color:var(--ink);display:flex;gap:14px;align-items:center;padding-bottom:12px;border-bottom:1px solid var(--line)}
.analysis p{font-size:10.5px;line-height:15px;color:#55585d;padding:13px 0;border-bottom:1px solid var(--line)}
.daterange{left:323px;top:500px;width:577px;height:55px;border:1px solid var(--line);border-radius:4px;font-size:8.5px;color:var(--muted);display:flex;align-items:flex-end;justify-content:center;padding-bottom:12px}
.scrim{left:0;top:0;width:1200px;height:675px;background:rgba(0,0,0,.58)}
.modal{left:300px;top:151px;width:600px;height:373px;background:#fff;border-radius:5px}
.modal .head{height:66px;display:flex;align-items:center;justify-content:space-between;padding:0 30px;border-bottom:1px solid var(--line)}
.closebtn{width:30px;height:30px;border:1px solid #c9cbce;border-radius:3px;display:flex;align-items:center;justify-content:center}
.msec{position:absolute;left:30px;width:540px}
.msec .group-head{gap:9px}
.chips{display:flex;flex-wrap:wrap;gap:7px 6px;margin:6px 0 0 21px}
.chip{height:27px;padding:0 11px;border:1px solid #d6d8db;border-radius:3px;font-size:11px;color:#45484d;display:flex;align-items:center}
.chip.selected{border:1.5px solid var(--red);box-shadow:0 0 0 1px #fff inset;color:var(--ink);font-weight:500;outline:1px solid #f0b8ba}
</style>
</head>
<body>
<header class="abs topbar">LexiPath Tutor&nbsp;<svg width="8" height="6" viewBox="0 0 8 6"><path d="M0 1h8L4 5z" fill="#cfd2d6"/></svg>
  <div class="icons">
    <svg width="13" height="13" viewBox="0 0 16 16"><circle cx="8" cy="8" r="5" fill="none" stroke="#cfd2d6" stroke-width="3" stroke-dasharray="3 2"/><circle cx="8" cy="8" r="2" fill="#cfd2d6"/></svg>
    <svg width="13" height="13" viewBox="0 0 16 16"><path d="M8 1l6 2v5c0 4-3 6-6 7-3-1-6-3-6-7V3z" fill="#cfd2d6"/><path d="M5 8l2 2 4-4" stroke="#1c1f23" stroke-width="1.6" fill="none"/></svg>
    <svg width="22" height="13" viewBox="0 0 26 16"><circle cx="8" cy="8" r="7" fill="#cfd2d6"/><circle cx="8" cy="6" r="2.5" fill="#1c1f23"/><path d="M3.5 12.5c2-3 7-3 9 0" fill="#1c1f23"/><path d="M19 6l3 3 3-3" stroke="#cfd2d6" fill="none" stroke-width="1.4"/></svg>
  </div>
</header>

<nav class="abs mainnav">
  <div class="navitem active"><svg width="11" height="11" viewBox="0 0 12 12"><path d="M6 1L1 6h1.5v5h3V8h1v3h3V6H11z" fill="#cfd2d6"/></svg>LexiPath Tutor</div>
  <div class="navitem"><svg width="14" height="12" viewBox="0 0 14 12"><path d="M1 3l4-2 4 2 4-2v8l-4 2-4-2-4 2z" fill="#cfd2d6"/></svg>Daily English</div>
  <div class="navitem"><svg width="10" height="12" viewBox="0 0 10 12"><rect x="0" y="0" width="10" height="12" fill="#cfd2d6"/><g fill="#1c1f23"><rect x="2" y="2" width="2" height="2"/><rect x="6" y="2" width="2" height="2"/><rect x="2" y="6" width="2" height="2"/><rect x="6" y="6" width="2" height="2"/></g></svg>Business</div>
</nav>

<aside class="abs vocab">
  <div class="abs select" style="left:18px;top:18px;width:168px">All Categories <svg width="10" height="6" viewBox="0 0 10 6"><path d="M1 1l4 4 4-4" stroke="#c8161d" fill="none" stroke-width="1.4"/></svg></div>
  <div class="abs iconbtn" style="left:192px;top:18px"><svg width="11" height="11" viewBox="0 0 12 12"><path d="M7 1h4v4M11 1L7 5M5 11H1V7M1 11l4-4" stroke="#c8161d" fill="none" stroke-width="1.3"/></svg></div>
  <div class="group" style="top:61px">
    <div class="group-head"><svg width="12" height="12" viewBox="0 0 12 12"><circle cx="6" cy="7" r="4.3" fill="none" stroke="#1f2124" stroke-width="1.3"/><path d="M6 7V4.5M4.5 1h3" stroke="#1f2124" stroke-width="1.3"/></svg>Short-Term Memory<svg class="info" width="12" height="12" viewBox="0 0 12 12"><circle cx="6" cy="6" r="5.3" fill="none" stroke="#aaa"/><path d="M6 5v4" stroke="#aaa"/></svg></div>
    <div class="word current" style="margin-top:5px;height:28px">Grab</div>
  </div>
  <div class="group" style="top:132px">
    <div class="group-head"><svg width="12" height="12" viewBox="0 0 12 12"><rect x="3" y="3" width="6" height="6" fill="none" stroke="#1f2124" stroke-width="1.3"/><path d="M4.5 1v2M7.5 1v2M4.5 9v2M7.5 9v2M1 4.5h2M1 7.5h2M9 4.5h2M9 7.5h2" stroke="#1f2124"/></svg>Working Memory<svg class="info" width="12" height="12" viewBox="0 0 12 12"><circle cx="6" cy="6" r="5.3" fill="none" stroke="#aaa"/><path d="M6 5v4" stroke="#aaa"/></svg></div>
    <div style="margin-top:3px">
      <div class="word">Cool Down</div><div class="word">Crave</div><div class="word">Go For</div><div class="word">Go-To</div><div class="word">In The Mood For</div><div class="word">Grab</div><div class="word">Sip</div><div class="word">Soothing</div>
    </div>
  </div>
  <div class="abs" style="left:216px;top:163px;width:3px;height:175px;background:#d0d2d5;border-radius:2px"></div>
  <div class="group" style="top:396px">
    <div class="group-head"><svg width="12" height="12" viewBox="0 0 12 12"><rect x="2" y="5" width="8" height="6" rx="1" fill="none" stroke="#1f2124" stroke-width="1.3"/><path d="M4 5V3.5a2 2 0 014 0V5" fill="none" stroke="#1f2124" stroke-width="1.3"/></svg>Long-Term Memory<svg class="info" width="12" height="12" viewBox="0 0 12 12"><circle cx="6" cy="6" r="5.3" fill="none" stroke="#aaa"/><path d="M6 5v4" stroke="#aaa"/></svg></div>
    <div class="word" style="margin-top:3px">Give It A Try</div>
  </div>
</aside>

<main>
  <div class="abs title">Grab <svg width="14" height="14" viewBox="0 0 14 14"><path d="M7 1l1.8 4 4.2.4-3.2 2.8 1 4.2L7 10.2 3.2 12.4l1-4.2L1 5.4l4.2-.4z" fill="var(--star)"/></svg></div>
  <div class="abs steps">
    <span class="step done"><svg width="14" height="14" viewBox="0 0 14 14"><circle cx="7" cy="7" r="7" fill="#1f9d55"/><path d="M4 7l2 2 4-4" stroke="#fff" fill="none" stroke-width="1.4"/></svg>Review 1</span><span class="dots"></span>
    <span class="step done"><svg width="14" height="14" viewBox="0 0 14 14"><circle cx="7" cy="7" r="7" fill="#1f9d55"/><path d="M4 7l2 2 4-4" stroke="#fff" fill="none" stroke-width="1.4"/></svg>Review 2</span><span class="dots"></span>
    <span class="step cur"><svg width="14" height="14" viewBox="0 0 14 14"><circle cx="7" cy="7" r="6.3" fill="#fff" stroke="#ccc"/><circle cx="7" cy="7" r="3" fill="#c8161d"/></svg>Review 3</span><span class="dots"></span>
    <span class="step todo"><svg width="14" height="14" viewBox="0 0 14 14"><circle cx="7" cy="7" r="6.3" fill="none" stroke="#bbb"/></svg>Review 4</span>
  </div>
  <div class="abs start"><svg width="10" height="10" viewBox="0 0 10 10"><path d="M1.5 1l7 4-7 4z" fill="none" stroke="#fff" stroke-width="1.2"/></svg>Start Review</div>
  <div class="abs hr" style="left:292px;top:92px;width:908px"></div>
  <div class="abs desc"><svg width="18" height="17" viewBox="0 0 18 17"><rect x="1" y="1" width="12" height="13" fill="none" stroke="#1f2124" stroke-width="1.3"/><circle cx="11" cy="10" r="3.3" fill="#fff" stroke="#1f2124" stroke-width="1.3"/><path d="M13.5 12.5l3 3" stroke="#1f2124" stroke-width="1.5"/></svg>Description</div>
  <section class="abs analysis">
    <h2><svg width="20" height="18" viewBox="0 0 20 18"><circle cx="10" cy="6" r="3" fill="none" stroke="#1f2124" stroke-width="1.3"/><path d="M4 17c0-4 3-6 6-6s6 2 6 6" fill="none" stroke="#1f2124" stroke-width="1.3"/><circle cx="3" cy="4" r="1.3" fill="#1f2124"/><circle cx="17" cy="4" r="1.3" fill="#1f2124"/></svg>LexiPath Tutor Learning Analysis</h2>
    <p>Lorem ipsum dolor sit amet, consectetur adipiscing elit, sed do eiusmod tempor incididunt ut labore et dolore magna aliqua.</p>
    <p>Ut enim ad minim veniam, quis nostrud exercitation ullamco laboris nisi ut aliquip ex ea commodo consequat.</p>
    <p>Excepteur sint occaecat cupidatat non proident, sunt in culpa qui officia deserunt mollit anim id est laborum.</p>
    <p style="border-bottom:0">Duis aute irure dolor in reprehenderit in voluptate velit esse cillum dolore eu fugiat nulla pariatur.</p>
  </section>
  <div class="abs daterange">Date Range</div>
</main>

<div class="abs scrim"></div>

<div class="abs modal" role="dialog" aria-label="All vocabulary">
  <div class="head">
    <div class="select" style="width:210px">All Categories <svg width="10" height="6" viewBox="0 0 10 6"><path d="M1 1l4 4 4-4" stroke="#c8161d" fill="none" stroke-width="1.4"/></svg></div>
    <div class="closebtn"><svg width="10" height="10" viewBox="0 0 10 10"><path d="M1 1l8 8M9 1L1 9" stroke="#c8161d" stroke-width="1.4"/></svg></div>
  </div>
  <div class="msec" style="top:92px">
    <div class="group-head"><svg width="12" height="12" viewBox="0 0 12 12"><circle cx="6" cy="7" r="4.3" fill="none" stroke="#1f2124" stroke-width="1.3"/><path d="M6 7V4.5M4.5 1h3" stroke="#1f2124" stroke-width="1.3"/></svg>Short-Term Memory</div>
    <div class="chips"><span class="chip selected">Grab</span></div>
  </div>
  <div class="msec" style="top:173px">
    <div class="group-head"><svg width="12" height="12" viewBox="0 0 12 12"><rect x="3" y="3" width="6" height="6" fill="none" stroke="#1f2124" stroke-width="1.3"/><path d="M4.5 1v2M7.5 1v2M4.5 9v2M7.5 9v2M1 4.5h2M1 7.5h2M9 4.5h2M9 7.5h2" stroke="#1f2124"/></svg>Working Memory</div>
    <div class="chips" style="width:480px"><span class="chip">Cool Down</span><span class="chip">Crave</span><span class="chip">Go For</span><span class="chip">Go-To</span><span class="chip">In The Mood For</span><span class="chip">Grab</span><span class="chip">Sip</span><span class="chip">Soothing</span><span class="chip">Stick With</span><span class="chip">Throw In / Throw On</span></div>
  </div>
  <div class="msec" style="top:287px">
    <div class="group-head"><svg width="12" height="12" viewBox="0 0 12 12"><rect x="2" y="5" width="8" height="6" rx="1" fill="none" stroke="#1f2124" stroke-width="1.3"/><path d="M4 5V3.5a2 2 0 014 0V5" fill="none" stroke="#1f2124" stroke-width="1.3"/></svg>Long-Term Memory</div>
    <div class="chips"><span class="chip">Give It A Try</span></div>
  </div>
</div>
</body>
</html>
```